Letterhead for a German Distribution/Manufacturing Company

We need a professional Letterhead in a unique Design.
not to playful.
The Letterhead has to show show that we are a international company with headquater in Germany.
all details like adress, Vat Tax Number, Bank Accout, Eori, email, Company number has to be on the Letterhead.
for example use: VAT TAX DE5470318 Bank Account: Kestrel Bank IBAN DE412058731ß204683 Swift: MORV0417352 EORI 3150428697 Company Number: HRB 51806 Adress: VOLMINTA UG Ahornweg 7 Postal Code 06384 City Kellbrunn Country: Germany Email: info@volminta-example.com
the design can be colored but doesnt have to be
Industry/Entity Type
Manufacturing and international distribution
Requirements
Must have
- show that we are a international company with headquater in Germany. our company infos and logo

```html
<!DOCTYPE html>
<html lang="en">
<head>
<meta charset="utf-8">
<title>Volminta Letterhead</title>
<link rel="stylesheet" href="https://fonts.googleapis.com/css2?family=Barlow:wght@400;500&family=Montserrat:wght@400;700&display=swap">
<style>
  :root {
    --backdrop: #e4e5e6;
    --paper: #ffffff;
    --ink: #1f1f1f;
    --brand: #3c3c3c;
    --muted: #555555;
    --sign-tone: #ececec;
  }
  * { margin: 0; padding: 0; box-sizing: border-box; }
  html, body { width: 1200px; height: 1200px; overflow: hidden; background: var(--backdrop); }
  .letterhead {
    position: absolute; left: 211px; top: 50px; width: 778px; height: 1100px;
    background: var(--paper); box-shadow: 0 6px 24px rgba(0,0,0,0.12);
    font-family: "Barlow", sans-serif; color: var(--ink);
  }
  .brand { position: absolute; left: 70px; top: 112px; display: flex; align-items: center; gap: 14px; }
  .brand-dot { width: 44px; height: 44px; border-radius: 50%; background: var(--brand); }
  .brand-name { font-family: "Montserrat", sans-serif; font-weight: 400; font-size: 38px; letter-spacing: 1px; color: var(--brand); }
  .sender { position: absolute; left: 500px; top: 62px; font-family: "Montserrat", sans-serif; font-size: 11px; line-height: 1.4; color: var(--ink); }
  .sender .mail { display: flex; align-items: center; gap: 6px; margin-left: 20px; }
  .recipient { position: absolute; left: 92px; top: 272px; font-size: 15px; line-height: 1.3; letter-spacing: 0.5px; }
  .salutation { position: absolute; left: 118px; top: 400px; font-size: 15px; letter-spacing: 0.5px; }
  .body-copy { position: absolute; left: 132px; top: 440px; width: 590px; font-size: 14.5px; line-height: 1.62; letter-spacing: 0.4px; }
  .signature { position: absolute; left: 228px; top: 740px; width: 190px; height: 52px; background: linear-gradient(90deg, var(--sign-tone), #f6f6f6); border-radius: 4px; }
  .closing { position: absolute; left: 228px; top: 806px; font-size: 15px; letter-spacing: 0.5px; }
  .footer-rule { position: absolute; left: 0; top: 0; }
  .footer-mark { position: absolute; left: 124px; top: 962px; width: 38px; height: 38px; border-radius: 50%; background: var(--brand); }
  .footer-details { position: absolute; left: 186px; top: 962px; display: flex; gap: 16px; font-family: "Montserrat", sans-serif; font-size: 11.5px; line-height: 1.35; color: var(--ink); }
  .footer-details b { font-weight: 700; }
  .footer-details .sep { width: 1px; height: 30px; background: var(--muted); transform: skewX(-20deg); }
</style>
</head>
<body>
<main class="letterhead">
  <div class="brand"><span class="brand-dot"></span><span class="brand-name">VOLMINTA</span></div>

  <address class="sender" style="font-style:normal">
    VOLMINTA UG Ahornweg 7<br>
    Postal Code 06384<br>
    City Kellbrunn Country: Germany<br>
    <span class="mail">
      <svg width="10" height="8" viewBox="0 0 10 8"><rect x="0.5" y="0.5" width="9" height="7" fill="none" stroke="#333"/><path d="M0.5 0.5 L5 4.5 L9.5 0.5" fill="none" stroke="#333"/></svg>
      info@volminta-example.com
    </span>
  </address>

  <div class="recipient">
    Mr. John Doe<br>President<br>Strategy Accountants<br>111 Street Name,<br>City State, 12345
  </div>

  <p class="salutation">Dear :</p>

  <p class="body-copy">
    Lorem ipsum dolor sit amet, consectetur adipiscing elit. Aenean ut ipsum eget massa hendrerit vestibulum vel in velit. Donec pretium neque velit. Aliquam porta lectus nec mauris ornare venenatis. Vivamus non est turpis, et cursus sem. Mauris vehicula erat in diam auctor at bibendum nisl lacinia. Integer Morbi imperdiet neque vehicula nunc convallis gravida. Vestibulum iaculis pretium placerat. Consequat, est sit amet facilisis eleifend, nibh nibh varius orci, eget dapibus arcu dui non purus. Pellentesque in magna mauris. Duis enim sapien, dictum vitae condimentum a, pulvinar vel lacus. Mauris et molestie nibh. Vestibulum vitae nulla at metus elementum porta sit amet interdum elit. Nulla sollicitudin neque eu nulla volutpat congue. Etiam pellentesque, velit id dapibus fermentum, turpis sapien ornare dui, ac tincidunt ligula odio congue purus. Nunc sed ante dui, in porta lectus. Cras nec sem lorem. In hac habitasse platea dictumst. Maecenas id diam quis dui porta tristique. Sed id egestas felis. Donec ullamcorper mattis posuere. Phasellus fermentum eleifend tortor vel dapibus. Vestibulum ante ipsum.
  </p>

  <div class="signature" role="img" aria-label="Handwritten signature of Jonathan Doe"></div>
  <p class="closing">Sincerely,</p>

  <svg class="footer-rule" width="778" height="1100" viewBox="0 0 778 1100">
    <path d="M112 958 L112 1000 Q112 1030 142 1030 L778 1030" fill="none" stroke="var(--brand)" stroke-width="5"/>
    <path d="M98 958 L98 1004 Q98 1044 138 1044 L778 1044" fill="none" stroke="var(--brand)" stroke-width="5"/>
  </svg>
  <span class="footer-mark"></span>

  <div class="footer-details">
    <div><b>VAT TAX</b> DE5470318<br><b>Swift:</b> MORV0417352</div>
    <span class="sep"></span>
    <div><b>Bank Account:</b> Kestrel Bank<br><b>EORI</b> 3150428697</div>
    <span class="sep"></span>
    <div><b>IBAN</b> DE412058731ß204683<br><b>Company Number:</b> HRB 51806</div>
  </div>
</main>
</body>
</html>
```